Commercial Real Estate Corporate Site

Our company sells an ERP software to Commercial Real Estate Companies, this project is part of a marketing and sales relaunch of the company.

See attached for PDF formatted Design brief

The software is a modular system where client’s can adopt one module at a time. Our customers are corporate clients who own between 10M and 10B of real estate properties. The typical customer is from the IT or the Financial arm of the company. Our differentiation in the market is that our system is built on a no-code environment, so making changes for the client is quick. Incumbents in the market have long implementation cycles, and customization is often not possible. Competitors are Quorvel, TKB, PlotNest, Vumora.

We need a design for our site which will be implemented into Brevo Forge. **All designs must be compatible with the newest version of Brevo Forge.**

We have produced the following attached assets to use in the website design.:

1. Logo
2. Brand Guidelines
3. Content for Pages
4. Menu Structures
5. Illustrations (modules)
I can't attach them because the files are too big, so they're in this google drive instead:
https://files.examplestore.net/share/k29Xa7Lq0Pz3Rt8MwB5nYc4Hv1Jd6Fe?mode=view

The mechanic for our sales process is as follows:

1. We find on module from our application that a client is interested in. The illustrations that we’ve attached represent the individual modules (elements) of the software.
1. For instance, one of our current customers has purchased a commissions module from us which helps calculate the commission that brokers receive for buying and selling their properties.
2. We provide immense value through the module, and then keep in sales communication with the client to determine which other modules we can implement for them.
1. For instance, in the example above, the client is so happy with the commissions module that they want to start working with our leasing module as well. In the next business quarter, they also choose to add our financials module to their business systems.

### Logo

Attached

### Brand Guidelines

Attached

We are open to suggestions on the secondary colour palette.

### **Site Copy**

**We require the following pages to be created; For now, we will do one Market Page, one Product Page, and one Platform / Services Page, and we will use those as inspiration to create the other dozen Marketing Pages and 30 or so Product Pages.**

**Homepage**

Attached

**Market Page** - look at the quorvel site under the Office, Industrial, Retail (https://www.quorvel.com/products/quorvel-commercial-suite/)

**Product** - One product provided, but there will be 30 - look at the vumora page

(https://www.vumora.com/products/general-accounting)

**Platform / Services Page** - pages that tell the story of our platform and services, content to be provided - the platform will use our modules as it highlights the story of the configurability and composability of the platform. Instead of the icons that they use, we want to use our modules.

- https://www.pelbrix.com/enterprise-applications-platform
- https://www.pelbrix.com/cloud-architecture

**Team Page** - just add sample content for starters (6 Team Members to start)

**Schedule Demo Page** - the call to action for all pages

(https://go.vumora.com/schedule-demo.html)

### Menu Structure

The menu is provided as an attachment.

### Illustrations Information

A note about the illustrations - we have provided an illustrator file with the modules, and if you’d like you can arrange the in any way that you’d like to. We especially like when the modules are positioned like a periodic table of the elements.

Our existing clients are

- Torvane Coop - https://www.torvanecoop.com/real-estate/
- Dalsworth Realestate https://dalsworth.com

Our competitors are

- Quorvel - www.quorvel.com
- TKB - [www.tkbsoftware.com](https://www.tkbsoftware.com/) (we don’t like how this one looks)
- Vumora - www.vumora.com
- Plotnest - www.plotnest.com

Design inspiration

- https://lark-studio.brevosite.com/velmo
- Corporate
- Established
- Modern

### Stock Images Guidance

- https://www.drafta.net/design/QXR7Lm2TpWz/Hk9vN3c8Yd41-FbqsaZRr/edit?utm_content=QXR7Lm2TpWz&utm_campaign=designshare&utm_medium=link2&utm_source=sharebutton

Target Market(s)

Commercial Real Estate Companies - they typically own a portfolio of 50 - 5000 real estate properties and need a software to manage it all.

Coding

Coded - Design and coding required

Number of Pages Required

5+ page

Font styles to use
Other font styles liked:
• Fonts defined in brand guideline

Requirements
Must have
• Brevo Forge, Use the Elemental Design, Download ai.zip and png.zip Use Brand Guideline,
Nice to have
• Check design breif

```html
<!DOCTYPE html>
<html lang="en">
<head>
<meta charset="utf-8">
<title>Corvanta — Enterprise Applications Platform for Real Estate</title>
<link rel="stylesheet" href="https://fonts.googleapis.com/css2?family=Audiowide&family=Poppins:wght@400;500;600&display=swap">
<style>
:root{
  --red:#e20a0a;
  --ink:#111111;
  --body:#333333;
  --muted:#555555;
  --white:#ffffff;
  --panel:#f3f3f3;
  --display:"Audiowide", sans-serif;
  --text:"Poppins", sans-serif;
}
*{box-sizing:border-box;margin:0;padding:0}
html,body{width:1200px;height:3423px;overflow:hidden;background:var(--white)}
body{position:relative;font-family:var(--text);color:var(--body)}
.abs{position:absolute}
a{color:inherit;text-decoration:none}
.btn{position:absolute;display:flex;align-items:center;justify-content:center;background:var(--red);color:var(--white);font:600 15px var(--text);border-radius:3px;box-shadow:0 2px 6px rgba(0,0,0,.15)}
.display{font-family:var(--display);color:var(--ink);font-weight:400;letter-spacing:.5px}
.photo{position:absolute}
.para{font-size:15px;line-height:25px;text-align:justify;color:var(--body)}

/* header */
.site-header{position:absolute;top:0;left:0;width:1200px;height:76px;background:var(--white)}
.brand{position:absolute;display:flex;align-items:center;gap:8px;white-space:nowrap}
.brand-mark{width:34px;height:34px;border:5px solid var(--red);flex:none}
.brand-name{font:600 34px var(--text);color:var(--red);letter-spacing:1px}
.nav a{position:absolute;top:26px;font:500 15px var(--text);color:var(--ink)}
.nav a.active{color:var(--red)}

/* hero */
.hero{position:absolute;top:76px;left:0;width:1200px;height:644px;background:linear-gradient(160deg,#0a0f1c 0%,#15213f 40%,#27406c 70%,#0d1426 100%)}
.hero-title{position:absolute;left:112px;top:230px;font:400 64px var(--display);color:var(--white);letter-spacing:2px}
.social{position:absolute;left:28px;width:34px;height:34px;border-radius:50%;background:var(--white);display:flex;align-items:center;justify-content:center}
.scroll-line{position:absolute;left:44px;top:260px;width:2px;height:180px;background:var(--red)}
.scroll-label{position:absolute;left:-8px;top:395px;transform:rotate(-90deg);font:500 15px var(--text);color:var(--white)}
.dot{position:absolute;top:586px;width:13px;height:13px;border-radius:50%;border:2px solid var(--white)}
.dot.on{background:var(--red)}

.center{position:absolute;left:0;width:1200px;text-align:center}
.clients{position:absolute;left:123px;top:1391px;width:954px;height:196px;background:var(--red)}
.clients-title{position:absolute;left:150px;top:80px;font:400 26px var(--display);color:var(--white);white-space:nowrap}
.client-name{position:absolute;top:84px;font:600 18px var(--text);color:var(--white);display:flex;align-items:center;gap:8px;white-space:nowrap}
.client-name i{display:block;width:16px;height:16px;border-radius:50%;background:var(--white);flex:none}

.accent-bar{position:absolute;width:5px;height:42px;background:var(--red)}
.h-section{font-size:28px}
.sub{font:500 21px var(--text);color:var(--ink)}

.footer-col h4{font:400 16px var(--display);color:var(--ink)}
.footer-col .rule{width:50px;height:2px;background:var(--red);margin:14px 0 12px}
.footer-col li{list-style:none;font-size:12px;line-height:23px;color:var(--muted)}
</style>
</head>
<body>

<header class="site-header">
  <div class="brand" style="left:112px;top:16px">
    <span class="brand-mark"></span>
    <span class="brand-name">CORVANTA</span>
  </div>
  <nav class="nav">
    <a class="active" style="left:613px">Home</a>
    <a style="left:692px">About</a>
    <a style="left:771px">Platform</a>
    <a style="left:868px">Clients</a>
  </nav>
  <a class="btn" style="left:941px;top:11px;width:147px;height:47px">Contact Us</a>
</header>

<section class="hero" role="img" aria-label="Night view of a curved modern pavilion with a city skyline behind">
  <span class="social" style="top:205px"><svg width="14" height="14" viewBox="0 0 14 14"><circle cx="7" cy="7" r="5" fill="var(--red)"/></svg></span>
  <span class="social" style="top:248px"><svg width="16" height="12" viewBox="0 0 16 12"><rect x="1" y="1" width="14" height="10" rx="1" fill="var(--red)"/><path d="M1 1l7 6 7-6" stroke="#fff" stroke-width="1.4" fill="none"/></svg></span>
  <span class="scroll-line"></span>
  <span class="scroll-label">Scroll Down</span>
  <h1 class="hero-title">ELEMENTAL</h1>
  <a class="btn" style="left:116px;top:314px;width:146px;height:46px">Schedule Demo</a>
  <span class="dot" style="left:112px"></span>
  <span class="dot on" style="left:133px"></span>
  <span class="dot" style="left:155px"></span>
</section>

<section class="welcome">
  <h2 class="display center" style="top:790px;font-size:36px">WELCOME TO CORVANTA</h2>
  <p class="center" style="top:847px;font-size:20px;line-height:32px;color:var(--ink)">an infinitely composable Enterprise Applications Platform (EAP)<br>for real estate.</p>
  <div class="abs" style="left:110px;top:912px;width:176px;height:173px;background:var(--red)"></div>
  <div class="photo" style="left:140px;top:940px;width:439px;height:363px;background:linear-gradient(135deg,#dfe3ea 0%,#aeb6c4 45%,#2f3fc0 100%)" role="img" aria-label="Close-up of a facade covered in reflective metal discs against blue"></div>
  <div class="abs" style="left:618px;top:970px;width:472px">
    <p class="para">Far beyond what’s possible with tired, legacy real estate ERP software, Corvanta offers a complete industry solution, architected as flexible modules that can be assembled and configured into an infinite combination of processes and workflows.</p>
    <p class="para" style="margin-top:17px">The Corvanta Enterprise solution seamlessly delivers both modular software and bundled services to transform your business with less risk, greater security, and lower cost.</p>
  </div>
  <a class="btn" style="left:618px;top:1205px;width:147px;height:47px">Learn More</a>
</section>

<section class="clients">
  <h2 class="clients-title">OUR CLIENTS</h2>
  <span class="abs" style="left:431px;top:58px;width:4px;height:76px;background:var(--white)"></span>
  <span class="client-name" style="left:462px"><i></i>Torvane Coop</span>
  <span class="client-name" style="left:640px"><i></i>Dalsworth National</span>
</section>

<section class="about">
  <h2 class="display center" style="top:1668px;font-size:36px">ABOUT</h2>
  <p class="center sub" style="top:1722px">One Solution - Infinite Possibilities</p>

  <span class="accent-bar" style="left:112px;top:1845px"></span>
  <h3 class="display h-section abs" style="left:124px;top:1848px">CORVANTA ENTERPRISE</h3>
  <p class="para abs" style="left:114px;top:1912px;width:444px">Corvanta was born from decades of real estate enterprise software development and implementation experience — spanning hundreds of blue chip global real estate investment firms. But Corvanta is unlike anything you’ve experienced before.</p>
  <a class="btn" style="left:114px;top:2062px;width:146px;height:47px">Learn More</a>
  <div class="photo" style="left:600px;top:1790px;width:488px;height:362px;background:linear-gradient(150deg,#5c6880 0%,#c8ccd4 45%,#eef0f3 70%,#8d96a8 100%)" role="img" aria-label="Interior of a futuristic white atrium with curved balconies"></div>

  <div class="photo" style="left:112px;top:2152px;width:488px;height:362px;background:linear-gradient(160deg,#aab3b5 0%,#dfe3e2 45%,#b9c3c6 100%)" role="img" aria-label="Sweeping white curved building facade against a pale sky"></div>
  <span class="accent-bar" style="left:630px;top:2180px;height:72px"></span>
  <h3 class="display abs" style="left:643px;top:2180px;width:450px;font-size:24px;line-height:36px">THE MODULES OF CORVANTA (AKA PLATFORM?)</h3>
  <p class="sub abs" style="left:630px;top:2270px">Simple - Secure - Scalable</p>
  <p class="para abs" style="left:632px;top:2309px;width:446px">Corvanta is the real estate industry’s only infinitely composable Enterprise Applications Platform (EAP), ensuring scalability, security, auditability, and compliance. Corvanta is a complete solution covering all functional areas of real estate investment, development, finance, accounting, management and operations.</p>
  <a class="btn" style="left:632px;top:2478px;width:147px;height:47px">Learn More</a>
</section>

<section class="platform">
  <div class="abs" style="left:0;top:2602px;width:651px;height:493px;background:var(--panel)"></div>
  <h2 class="display abs" style="left:112px;top:2665px;font-size:36px">PLATFORM</h2>
  <p class="sub abs" style="left:112px;top:2713px">Stop settling for less than exactly what you want</p>
  <p class="para abs" style="left:113px;top:2760px;width:466px">Corvanta combines the best of all worlds in our Enterprise Applications Platform (EAP): the simplicity and scalability of custom, no-code, software and the security and confidence of a complete, SOC 2 compliant industry solution. Our modular approach enables rapid innovation and re-invention of your business by casting off the shackles of legacy ERP technology and delivering a modern, agile solution that bridges the gaps for all of your real estate workflows.</p>
  <a class="btn" style="left:114px;top:2975px;width:146px;height:47px">Learn More</a>
  <div class="photo" style="left:651px;top:2610px;width:549px;height:485px;background:linear-gradient(160deg,#2a3fb8 0%,#7f95e8 40%,#c9d3f5 55%,#2535a0 80%,#0d1458 100%)" role="img" aria-label="Night view of a curved building with glowing blue balconies"></div>
</section>

<footer class="site-footer">
  <div class="brand" style="left:228px;top:3218px">
    <span class="brand-mark" style="width:40px;height:40px;border-width:6px"></span>
    <span class="brand-name" style="font-size:32px">CORVANTA</span>
  </div>
  <div class="footer-col abs" style="left:524px;top:3160px">
    <h4>QUICK LINKS</h4><div class="rule"></div>
    <ul><li>Home</li><li>About</li><li>Platform</li><li>Clients</li><li>Contact Us</li></ul>
  </div>
  <div class="footer-col abs" style="left:687px;top:3160px">
    <h4>LINKS</h4><div class="rule"></div>
    <ul><li>Copyright</li><li>Terms of Use</li><li>Privacy Policy</li><li>Accessibility</li><li>Sitemap</li></ul>
  </div>
  <div class="footer-col abs" style="left:852px;top:3160px">
    <h4>SUPPORT</h4><div class="rule"></div>
    <ul><li>Team</li><li>About Us</li><li>Careers</li><li>Our Values</li><li>Data Security</li></ul>
  </div>
  <div class="abs" style="left:110px;top:3350px;width:978px;height:1px;background:var(--red)"></div>
  <p class="center" style="top:3381px;font-size:14px;color:var(--muted)">©2024. All rights reserved.</p>
</footer>

</body>
</html>
```